Business Cards for a law firm

Business cards for our law firm. Use our silhoette logo and OAK PARTNERS - check our website (www.oakpartners.example)

Contact Information for Business Card

our silhouette logo, OAK PARTNERS, 800-555-0147, Dorian Pemberton, dorian@oakpartners.example

Requirements
Must have
• our silhouette logo, OAK PARTNERS, 800-555-0147, Dorian Pemberton, dorian@oakpartners.example

```html
<!DOCTYPE html>
<html lang="en">
<head>
<meta charset="utf-8">
<title>Oak Partners – Business Cards</title>
<link rel="stylesheet" href="https://fonts.googleapis.com/css2?family=Montserrat:wght@400;500;700&display=swap">
<style>
  :root {
    --navy: #1c3370;
    --paper: #ffffff;
    --ground: #e9eaee;
    --ink: #1c3370;
  }
  * { box-sizing: border-box; margin: 0; padding: 0; }
  html, body { width: 1200px; height: 801px; overflow: hidden; }
  body {
    background: var(--ground);
    font-family: "Montserrat", Arial, sans-serif;
    display: flex;
    align-items: center;
    justify-content: center;
    gap: 48px;
  }
  .card {
    position: relative;
    width: 540px;
    height: 309px;
    overflow: hidden;
    box-shadow: 0 10px 28px rgba(20, 25, 45, 0.22);
  }
  /* Front */
  .card--front {
    background: var(--navy);
    color: var(--paper);
    display: flex;
    flex-direction: column;
    align-items: center;
    justify-content: center;
  }
  .front__name {
    font-weight: 700;
    font-size: 38px;
    letter-spacing: 3px;
    transform: scaleX(1.12);
  }
  .front__web {
    margin-top: 6px;
    font-size: 11px;
    font-weight: 400;
    letter-spacing: 6.5px;
  }
  /* Back */
  .card--back { background: var(--paper); color: var(--ink); }
  .back__brand {
    position: absolute;
    left: 48px;
    top: 62px;
    display: flex;
    align-items: center;
    gap: 16px;
  }
  .brand__mark {
    width: 38px;
    height: 38px;
    background: var(--navy);
  }
  .brand__name {
    font-weight: 700;
    font-size: 34px;
    letter-spacing: 2.5px;
  }
  .back__band {
    position: absolute;
    left: 72px;
    top: 170px;
    width: 66px;
    height: 139px;
    background: var(--navy);
  }
  .back__person {
    position: absolute;
    left: 190px;
    top: 150px;
    font-size: 19px;
    font-weight: 400;
    letter-spacing: 1px;
    text-transform: uppercase;
  }
  .back__contacts {
    position: absolute;
    left: 190px;
    top: 190px;
    list-style: none;
    font-size: 13.5px;
    line-height: 24px;
  }
  .contact { display: flex; align-items: center; gap: 9px; }
  .contact svg { width: 12px; height: 12px; fill: var(--navy); flex: none; }
</style>
</head>
<body>
  <section class="card card--front" aria-label="Business card front">
    <h1 class="front__name">OAK PARTNERS</h1>
    <p class="front__web">www.oakpartners.example</p>
  </section>

  <section class="card card--back" aria-label="Business card back">
    <div class="back__brand">
      <span class="brand__mark"></span>
      <h2 class="brand__name">OAK PARTNERS</h2>
    </div>
    <div class="back__band"></div>
    <p class="back__person">Dorian Pemberton</p>
    <ul class="back__contacts">
      <li class="contact">
        <svg viewBox="0 0 24 24" aria-hidden="true"><path d="M6.6 10.8a15.1 15.1 0 0 0 6.6 6.6l2.2-2.2c.3-.3.7-.4 1-.2 1.1.4 2.3.6 3.6.6.6 0 1 .4 1 1V20c0 .6-.4 1-1 1A17 17 0 0 1 3 4c0-.6.4-1 1-1h3.5c.6 0 1 .4 1 1 0 1.3.2 2.5.6 3.6.1.3 0 .7-.2 1z"/></svg>
        800-555-0147
      </li>
      <li class="contact">
        <svg viewBox="0 0 24 24" aria-hidden="true"><path d="M2 5h20v14H2zm2 2v.5l8 5 8-5V7l-8 5z"/></svg>
        dorian@oakpartners.example
      </li>
      <li class="contact">
        <svg viewBox="0 0 24 24" aria-hidden="true"><path d="M12 2a10 10 0 1 0 0 20 10 10 0 0 0 0-20zm6.9 6h-3a15 15 0 0 0-1.3-4A8 8 0 0 1 18.9 8zM12 4c.8 1.2 1.5 2.5 1.9 4h-3.8c.4-1.5 1.1-2.8 1.9-4zM4.3 14a8 8 0 0 1 0-4h3.4a16 16 0 0 0 0 4zm.8 2h3a15 15 0 0 0 1.3 4A8 8 0 0 1 5.1 16zm3-8h-3a8 8 0 0 1 4.3-4c-.6 1.2-1 2.6-1.3 4zM12 20c-.8-1.2-1.5-2.5-1.9-4h3.8c-.4 1.5-1.1 2.8-1.9 4zm2.3-6H9.7a14 14 0 0 1 0-4h4.6a14 14 0 0 1 0 4zm.3 6c.6-1.2 1-2.6 1.3-4h3a8 8 0 0 1-4.3 4zm1.7-6a16 16 0 0 0 0-4h3.4a8 8 0 0 1 0 4z"/></svg>
        www.oakpartners.example
      </li>
    </ul>
  </section>
</body>
</html>
```